Cruise Booking Website

Cruise search and booking website

This project is a redesign of a cruise booking website we did a few years ago.

The current website is located here: http://voyage.pylonworks.example/en/

It's not fully functional but gives you ad idea how miserable the old design was.

All the information about cruises, cruise lines, destinations, ports and shore excursions will be similar to http://www.sailquest.example/
Actual search pages (form, results, single result, sailing and cabin selection, ship info, booking) will have EXACTLY the same info as sailquest.example

We like the style of http://harborfleetdesk.example, it's quite modern, good spacing, not overloaded with information. So you can use it as an example of what we like, not what we want as a final result for us. Please, don't copy it. The result should not be possible to resemble the harborfleetdesk.example, because our site has to be unique. This is important!
If you submit a design that clearly reminds another cruise site it will be rejected!

Also the mockup provided is just to give you the basic structure and show what information has to be present on the page. It doesn't mean the layout has to be the same as a mockup. The layout is up to the designer.

I've updated the mockup to be more generic so it doesn't confuse you:
https://files.boxvault.example/s/k7m2qp9wz4hx/Home%20page.png

When you're adding social sharing icons like plazanet/chirpline you have to use chinese ones instead:
https://files.boxvault.example/s/t3nr8vx5lc2e/chinese-social-icons.png
Originals: http://minilk.example/qR7t

We'll start with home page first and after it's approved inner pages can be designed.

I know the cost of the project doesn't look high, but the task is straight forward and doesn't require to be very original, it's better to follow existing design and layout patterns that proved to work well.
That's why I encourage you to choose a template to build the design on top of one of https://themeparlor.example/ themes if it will save the design work, will be easier and faster for you. So it will be more like a customization than a new design from scratch.

Mockups, site map and logo files:
- https://files.boxvault.example/sh/h48dm2rs73fkpw/QvnbW2Xz8e

Website tree:
- https://sheets.papernest.example/document/d/7xPqR2mLw9sTk4VbN8cHj3YzA6eUf5GdKo1iMnBv/edit?usp=sharing
Updates

So far a lot of designs are just copying http://www.harborfleetdesk.example/ - we don't like it!

We like the style of harborfleetdesk.example, it's quite modern, good spacing, not overloaded with information. So you can use it as an example of what we like, not what we want as a final result for us. Please, don't copy it. The result should not be possible to resemble the harborfleetdesk.example, because our site has to be unique. This is important!

Target Market(s)

Chinese travellers

Industry/Entity Type

Build

Requirements
Must have
• * White, blue and red
* Large spacing, not too much information cramped into a small space like sailquest.example or the current website
* More "hidden" info in popups, tabs and so on, so not to many things are visible at the same time
* Compatible with kestrel scaffold styling (for easier coding):
- http://kestrelkit.codeshelf.example/scaffold/index.html
- http://skinmarket.example/
* Feel free to propose to build the design on top of one of https://themeparlor.example/ themes if it will save the design work, will be easier and faster for you

```html
<!DOCTYPE html>
<html lang="en">
<head>
<meta charset="utf-8">
<title>海程邮轮 – Cruise Booking</title>
<link href="https://fonts.googleapis.com/css2?family=Source+Sans+3:wght@400;600;700&family=Noto+Sans+SC:wght@700&display=swap" rel="stylesheet">
<style>
:root{
  --blue:#1c6fb0;
  --blue-dark:#0f4f8a;
  --blue-deep:#0b3f70;
  --blue-light:#2d8fd3;
  --sky:#3aa0df;
  --orange:#f7931e;
  --orange-dark:#e2760a;
  --red:#d7262b;
  --text:#555;
  --muted:#888;
  --line:#dfe3e8;
  --white:#fff;
  --footer:#4a7fae;
  --footer-bar:#3f719d;
}
*{box-sizing:border-box;margin:0;padding:0}
html,body{width:938px;height:1200px;overflow:hidden}
body{position:relative;font-family:"Source Sans 3",sans-serif;color:var(--text);
  background:radial-gradient(ellipse at 50% 40%,#e9f1f8 0%,#9cc0de 35%,#3d77ad 70%,#245d96 100%)}
.abs{position:absolute}
.page{position:absolute;left:141px;top:0;width:657px;height:1200px;background:var(--white)}
/* header */
.logo{left:150px;top:24px;display:flex;align-items:center;gap:6px}
.logo-dot{width:36px;height:36px;border-radius:50%;background:var(--blue-light)}
.logo-name{font-family:"Noto Sans SC",sans-serif;font-size:27px;font-weight:700;color:var(--blue-dark);line-height:1}
.logo-url{left:192px;top:56px;font-size:8px;font-weight:700;color:var(--blue-dark);letter-spacing:.5px}
.account{left:621px;top:13px;font-size:9px;color:var(--blue)}
.social{left:706px;top:10px;display:flex;gap:3px}
.social span{width:17px;height:17px;border-radius:3px}
.phone{left:496px;top:40px;display:flex;gap:6px;align-items:center}
.phone-num{font-size:15px;font-weight:700;color:var(--blue);line-height:1}
.phone-sub{font-size:12px;color:#333;line-height:1.2}
.search{left:630px;top:51px;width:155px;height:18px;border:1px solid #ccc;border-radius:2px;font-size:7px;color:#999;padding:4px 8px}
/* nav */
.nav{left:141px;top:88px;width:657px;height:26px;background:linear-gradient(#2a85c8,#176bac);display:flex;border-bottom:1px solid var(--blue-deep)}
.nav a{font-size:8px;font-weight:700;color:var(--white);text-decoration:none;text-align:center;line-height:26px;border-right:1px solid #1a5f96}
.nav a.active{background:linear-gradient(#46aef0,#2590d8)}
/* search box */
.panel{background:linear-gradient(#2b86c7,#1b6aa9);border:1px solid #1a5f96;border-radius:2px;color:var(--white)}
.finder{left:155px;top:130px;width:194px;height:272px}
.finder h2{position:absolute;left:17px;top:12px;font-size:18px;font-weight:400}
.finder .rule{position:absolute;left:0;top:36px;width:100%;height:1px;background:#4d9ad3}
.lbl{font-size:9px;color:#e3f0fa}
.field{height:17px;background:linear-gradient(#fff,#d9dee3);border:1px solid #aab;border-radius:2px;font-size:7px;color:#333;padding:3px 7px;position:absolute}
.field::after{content:"";position:absolute;right:0;top:0;width:15px;height:100%;border-left:1px solid #aab}
.check{left:15px;top:303px;width:8px;height:8px;background:#fff;border:1px solid #999}
.btn-orange{left:170px;top:361px;width:165px;height:26px;border-radius:3px;background:linear-gradient(#fdab3b,var(--orange-dark));color:#fff;font-size:12px;font-weight:600;text-align:center;line-height:26px}
.newsletter{left:155px;top:420px;width:194px;height:232px}
.photo{background:linear-gradient(160deg,#48a9d6,#d9b48a 60%,#f2e0c8)}
.news-photo{left:10px;top:10px;width:174px;height:105px;border:3px solid #fff}
.news-title{left:15px;top:123px;font-size:11px;font-weight:600}
.news-sub{left:15px;top:140px;font-size:7px}
.email{left:15px;top:158px;width:169px;height:17px;background:#fff;border-radius:2px;color:#999;font-size:7px;padding:4px 37px}
.subscribe{left:15px;top:185px;width:69px;height:18px;background:var(--blue-deep);border-radius:2px;font-size:8px;text-align:center;line-height:18px}
.rules{left:18px;top:210px;font-size:8px}
/* content */
.crumbs{left:371px;top:130px;font-size:8px;color:var(--blue)}
.hero{left:367px;top:151px;width:415px;height:211px;background:linear-gradient(#cbe6f5 0%,#8cc4e2 20%,#4e9c5a 24%,#2f86c7 40%,#0f5e9e 100%)}
.hero-bar{left:367px;top:322px;width:415px;height:40px;background:rgba(12,30,48,.85);color:#fff;font-size:17px;font-weight:700;padding:9px 11px}
.dots{left:718px;top:339px;display:flex;gap:3px}
.dots span{width:7px;height:7px;border-radius:50%;background:#777}
.dots span:first-child{background:#ccc}
.tabs{left:367px;top:381px;display:flex;gap:2px}
.tabs span{height:24px;font-size:7px;color:#fff;text-align:center;line-height:24px;border-radius:2px 2px 0 0}
.tab-orange{background:linear-gradient(#fba63a,var(--orange-dark))}
.tab-blue{background:linear-gradient(#1c6eb0,var(--blue-deep))}
.tab-box{left:367px;top:406px;width:415px;height:325px;border:1px solid var(--line)}
.scroll{left:771px;top:407px;width:10px;height:323px;background:#f2f2f2;border-left:1px solid #ddd}
.scroll i{position:absolute;left:1px;top:11px;width:8px;height:32px;background:#ddd;border:1px solid #bbb}
.suite{left:381px;width:390px;height:107px;border-bottom:1px solid var(--line)}
.suite-img{left:0;top:12px;width:107px;height:82px;border:2px solid #fff;box-shadow:0 0 0 1px #ddd}
.suite h3{position:absolute;left:125px;top:16px;font-size:8px;font-weight:700;color:var(--blue)}
.suite p{position:absolute;left:125px;top:32px;width:265px;font-size:6.6px;line-height:12px;color:#777}
/* deals */
.deals{left:153px;top:748px;width:634px;height:168px;background:#cfdde9}
.deals-head{left:153px;top:748px;width:634px;height:24px;background:linear-gradient(#2a8fd7,#1a73b7);color:#fff;font-size:8px;padding:6px 14px}
.deals-head a{position:absolute;right:12px;top:6px;color:#fff;text-decoration:underline}
.card{top:784px;width:138px;height:116px;background:#fff;border:1px solid #d5dde4}
.card .photo{position:absolute;left:3px;top:3px;width:130px;height:73px}
.card p{position:absolute;left:8px;top:84px;font-size:7.5px;color:var(--blue-dark)}
.card b{position:absolute;left:8px;top:99px;font-size:8px;font-weight:400;color:var(--orange-dark)}
.arrow{top:828px;width:18px;height:24px;background:var(--orange);border-radius:12px}
/* partners */
.partners-title{left:153px;top:927px;font-size:12px;font-weight:700;color:var(--blue)}
.pager{top:928px;width:13px;height:13px;background:#ddd;border:1px solid #bbb}
.partner{top:952px;width:97px;height:48px;border:1px solid #d7dce0;display:flex;align-items:center;justify-content:center}
.partner i{width:44px;height:14px;border-radius:7px}
/* footer */
.footer{left:141px;top:1018px;width:657px;height:148px;background:var(--footer);color:#fff}
.footer h4{position:absolute;font-size:10px;font-weight:600}
.footer ul{position:absolute;list-style:none;font-size:6.6px;line-height:14.7px}
.about-logo{left:271px;top:49px;width:67px;height:67px;background:#fff;border:1px solid #ccc;display:flex;align-items:center;justify-content:center;gap:3px;flex-direction:column}
.about-logo span:first-child{width:26px;height:26px;border-radius:50%;background:var(--blue-light)}
.about-logo span:last-child{font-family:"Noto Sans SC",sans-serif;font-size:9px;font-weight:700;color:var(--blue-dark)}
.about-text{left:351px;top:59px;width:80px;font-size:8px;line-height:12px}
.contact{left:473px;top:46px;font-size:8px;line-height:13px}
.contact-line{left:473px;font-size:8px;display:flex;align-items:center;gap:5px}
.copy{left:141px;top:1166px;width:657px;height:34px;background:var(--footer-bar);color:#fff;font-size:6.5px;text-align:center;line-height:34px}
</style>
</head>
<body>
<div class="page"></div>

<!-- header -->
<div class="abs logo"><span class="logo-dot"></span><span class="logo-name">海程邮轮</span></div>
<div class="abs logo-url">www.haicheng.example</div>
<div class="abs account">Sign in &nbsp;|&nbsp; Signup</div>
<div class="abs social"><span style="background:var(--red)"></span><span style="background:var(--sky)"></span><span style="background:var(--orange)"></span><span style="background:#e14b4b"></span></div>
<div class="abs phone">
  <svg width="24" height="24" viewBox="0 0 24 24"><circle cx="12" cy="12" r="11" fill="none" stroke="#777" stroke-width="1.5"/><path d="M8 6c-1 1-1 3 1 6s4 5 6 5l1.5-1.5-2-2-1.5 1c-1-.5-2.5-2-3-3l1-1.5-2-2z" fill="#777"/></svg>
  <div><div class="phone-num">400 555 0188</div><div class="phone-sub">Call Us Today!</div></div>
</div>
<div class="abs search">SEARCH :</div>

<nav class="abs nav">
  <a style="width:68px">HOME</a><a style="width:95px">DESTINATIONS</a><a class="active" style="width:85px">CRUISE LINES</a><a style="width:82px">CRUISE INFO</a><a style="width:60px">DEALS</a><a style="width:95px">ONLINE BOOKING</a><a style="width:92px">CONTACT US</a><a style="width:80px;border-right:0">BLOG</a>
</nav>

<!-- find your cruise -->
<div class="abs panel finder">
  <h2>Find Your Cruise</h2><div class="rule"></div>
  <div class="abs lbl" style="left:16px;top:43px">Destination</div>
  <div class="field" style="left:16px;top:57px;width:162px">Destination name</div>
  <div class="abs lbl" style="left:17px;top:79px">Length</div>
  <div class="abs lbl" style="left:104px;top:79px">Month</div>
  <div class="field" style="left:16px;top:93px;width:73px">Length Area</div>
  <div class="field" style="left:103px;top:93px;width:75px"></div>
  <div class="abs lbl" style="left:15px;top:117px">Cruise Lines</div>
  <div class="field" style="left:14px;top:131px;width:165px">Any Cruise line</div>
  <div class="abs" style="left:15px;top:158px;font-size:10px">Number of Travelers</div>
  <div class="abs lbl" style="left:16px;top:175px">Age 25+</div>
  <div class="abs lbl" style="left:104px;top:175px">Age 0 to 24</div>
  <div class="field" style="left:15px;top:189px;width:73px">5</div>
  <div class="field" style="left:103px;top:189px;width:73px">0</div>
  <div class="abs check"></div>
  <div class="abs" style="left:27px;top:302px;font-size:7px;color:#d7e8f6">Check for senior rates</div>
</div>
<div class="abs btn-orange">Search Cruises</div>

<!-- newsletter -->
<div class="abs panel newsletter">
  <div class="abs photo news-photo" role="img" aria-label="Senior couple relaxing on deck chairs by a pool"></div>
  <div class="abs news-title">Cruise Deals Newsletter</div>
  <div class="abs news-sub">Subscribe to the best Cruise deals Now!</div>
  <div class="abs email">Email :</div>
  <div class="abs subscribe">Subscribe</div>
  <div class="abs rules">Contest Rules</div>
</div>

<!-- hero -->
<div class="abs crumbs">HOME &nbsp;›&nbsp; BREADCRUMBS</div>
<div class="abs hero" role="img" aria-label="White cruise ship sailing near a green island coast"></div>
<div class="abs hero-bar">AURORA LEGEND</div>
<div class="abs dots"><span></span><span></span><span></span><span></span><span></span></div>

<div class="abs tabs">
  <span class="tab-orange" style="width:97px">OVER VIEW</span>
  <span class="tab-blue" style="width:90px">DECKS</span>
  <span class="tab-orange" style="width:90px">ACTIVITIES</span>
</div>
<div class="abs tab-box"></div>
<div class="abs scroll"><i></i></div>

<div class="abs suite" style="top:409px">
  <div class="abs suite-img" style="background:linear-gradient(#2f4a75,#1e8a9b 60%,#6b4a2a)" role="img" aria-label="Resort pool at dusk with palm trees"></div>
  <h3>OCEAN SUITE</h3>
  <p>Bluewake Cruise Line was established in 1972 and is the world's largest cruise line. A Bluewake cruise is all about creating a fun, memorable vacation and their "Joy Ships" were designed to keep the fun going. On a Bluewake Cruise ship there is always so much to do. On deck there are pools, waterslides, golf, a Harbor Theater and activities galore to keep kids and adults of all ages entertained.</p>
</div>
<div class="abs suite" style="top:516px">
  <div class="abs suite-img" style="background:linear-gradient(#8a6a3a,#d7c3a0 55%,#5a3d22)" role="img" aria-label="Cabin with double bed and warm lighting"></div>
  <h3>OCEAN SUITE</h3>
  <p>Bluewake Cruise Line was established in 1972 and is the world's largest cruise line. A Bluewake cruise is all about creating a fun, memorable vacation and their "Joy Ships" were designed to keep the fun going. On a Bluewake Cruise ship there is always so much to do. On deck there are pools, waterslides, golf, a Harbor Theater and activities galore to keep kids and adults of all ages entertained.</p>
</div>
<div class="abs suite" style="top:623px;border-bottom:0">
  <div class="abs suite-img" style="background:linear-gradient(#c9902f,#e9c07a 50%,#8a3a1c)" role="img" aria-label="Golden-toned suite bedroom"></div>
  <h3>OCEAN SUITE</h3>
  <p>Bluewake Cruise Line was established in 1972 and is the world's largest cruise line. A Bluewake cruise is all about creating a fun, memorable vacation and their "Joy Ships" were designed to keep the fun going. On a Bluewake Cruise ship there is always so much to do. On deck there are pools, waterslides, golf, a Harbor Theater and activities galore to keep kids and adults of all ages entertained.</p>
</div>

<!-- last minute deals -->
<div class="abs deals"></div>
<div class="abs deals-head">LAST MINUTE DEALS :<a>View all last minute deals</a></div>
<div class="abs arrow" style="left:155px"><svg width="18" height="24"><path d="M11 8l-4 4 4 4" stroke="#fff" stroke-width="2" fill="none"/></svg></div>
<div class="abs arrow" style="left:766px"><svg width="18" height="24"><path d="M7 8l4 4-4 4" stroke="#fff" stroke-width="2" fill="none"/></svg></div>
<div class="abs card" style="left:170px"><div class="photo" style="background:linear-gradient(#2a8fd8,#8cc6e8 55%,#e9dcc4)" role="img" aria-label="Family running on a beach"></div><p>3 day cruise to the Bahamas</p><b>¥ 9000</b></div>
<div class="abs card" style="left:324px"><div class="photo" style="background:linear-gradient(#3f8fd0,#b59a6a 45%,#1fb3c9)" role="img" aria-label="Rocky island over turquoise sea"></div><p>3 day cruise to the Bahamas</p><b>¥ 9000</b></div>
<div class="abs card" style="left:478px"><div class="photo" style="background:linear-gradient(#8fc0e6,#6b8c8a 40%,#1aa8a0)" role="img" aria-label="City beach with high-rise hotels"></div><p>3 day cruise to the Bahamas</p><b>¥ 9000</b></div>
<div class="abs card" style="left:632px"><div class="photo" style="background:linear-gradient(120deg,#5a3620,#c88a4a 50%,#f0c080)" role="img" aria-label="Couple taking a photo together"></div><p>3 day cruise to the Bahamas</p><b>¥ 9000</b></div>

<!-- partners -->
<div class="abs partners-title">OUR RELIABLE PARTNERS</div>
<div class="abs pager" style="left:755px"></div><div class="abs pager" style="left:771px"></div>
<div class="abs partner" style="left:153px"><i style="background:var(--red)"></i></div>
<div class="abs partner" style="left:260px"><i style="background:var(--blue)"></i></div>
<div class="abs partner" style="left:367px"><i style="background:#5a6b80"></i></div>
<div class="abs partner" style="left:474px"><i style="background:var(--orange)"></i></div>
<div class="abs partner" style="left:581px"><i style="background:var(--sky)"></i></div>
<div class="abs partner" style="left:688px"><i style="background:var(--blue-light)"></i></div>

<!-- footer -->
<footer class="abs footer">
  <h4 style="left:21px;top:20px">Useful Pages</h4>
  <ul style="left:21px;top:38px"><li>About Us</li><li>Contact us</li><li>Blog</li><li>FAQ</li><li>Terms of Service</li><li>Payment info</li><li>Reward Points</li></ul>
  <h4 style="left:149px;top:20px">Cruise Infov</h4>
  <ul style="left:149px;top:38px"><li>Cruise news</li><li>Visa</li><li>Honeymoon cruises</li><li>Firsttime on a Cruise</li></ul>
  <h4 style="left:271px;top:24px">About haicheng.example</h4>
  <div class="abs about-logo"><span></span><span>海程邮轮</span></div>
  <div class="abs about-text">We're the most advanced cruise booking providr in china.</div>
  <h4 style="left:473px;top:24px">Contact Us</h4>
  <div class="abs contact">Marlin Works,Pte Ltd<br>Lantern Plaza x118, Quay Rd 7.2<br>Portvale 20931 Indonesia</div>
  <div class="abs contact-line" style="top:94px"><svg width="10" height="8"><path d="M0 3c3-3 7-3 10 0v1H7V3H3v1H0z M2 4h6l1 4H1z" fill="#fff"/></svg>(555) 014-2290 - (555)014-3381</div>
  <div class="abs contact-line" style="top:111px"><svg width="10" height="8"><rect x="0" y="0" width="10" height="8" fill="#fff"/><path d="M0 0l5 4 5-4" stroke="#4a7fae" fill="none"/></svg>hello@haicheng.example</div>
</footer>
<div class="abs copy">© 2013, haicheng.example. All rights reserved.</div>
</body>
</html>
```